Velan Tea Label & packaging for a premium tea brand. For local and global market

Create a look and feel for a box and rectangle tin. We are looking for a luxe packaging design for a new tea brand based in Kenya called 'Velan Tea'. Kenya is home to the finest teas in the world and Velan tea looks to embody that fact. Velan Tea uses the most premium of Kenyan Tea, Black tea, Purple tea, White Tea, Green tea, Hibiscus Tea and Moringa Tea. Velan Tea is handpicked from Kenya's highlands. This project will include the look and feel of the different teas described above. The copy on the main face of the box should read 'Premium Kenyan Tea' The box will contain 25 tagged tea bags, with a net weight of 50 gms.

On one side of the box will read 'packaging instructions' To fully savour this Velan premium tea, use one tea bag for each cup, add some freshly bolded water and wait for 2 minutes as you enjoy the sweet aroma of our tea, stir and serve' Ingredients : Black Tea, and for the others the same : Hibiscus Tea, Green Tea, Purple Tea, White tea. should also feature on the label: Produce of Kenya.

Target Market(s)

Premium

Industry/Entity Type

Agribusiness

Font styles to use
Script

Colors

Designer to choose colors to be used in the design.

Requirements
Must have
• Luxe look and feel
Nice to have
• I have attached the Velan tea logo and images of brands I'd lile the designer to be inspired by.
Should not have
• Green and yellow colours

```html
<!DOCTYPE html>
<html lang="en">
<head>
<meta charset="utf-8">
<title>Velan Tea – Green Tea Tin Label</title>
<link href="https://fonts.googleapis.com/css2?family=Libre+Baskerville:ital,wght@0,700;1,400&family=Montserrat:wght@300;400&family=Oswald:wght@400&display=swap" rel="stylesheet">
<style>
  :root {
    --backdrop: #a9abaf;
    --tin-black: #1b1919;
    --pattern-bronze: #8f6234;
    --pattern-shadow: #2a211a;
    --frame-bronze: #8a5c34;
    --label-burgundy: #5e2432;
    --brand-champagne: #ecd3bd;
    --label-ivory: #f6eee4;
    --rim-copper: #c49a78;
  }
  * { margin: 0; padding: 0; box-sizing: border-box; }
  html, body {
    width: 1200px; height: 639px; overflow: hidden;
    background: var(--backdrop);
  }
  .canvas {
    position: relative; width: 1200px; height: 639px;
    background: var(--backdrop);
  }
  .tin-face {
    position: absolute; left: 382px; top: 132px;
    width: 452px; height: 462px;
    background: var(--tin-black);
  }
  .rim-line {
    position: absolute; left: 0; top: 0; width: 100%; height: 3px;
    background: var(--rim-copper); opacity: .8;
  }
  .pattern-field {
    position: absolute; left: 0; top: 3px; width: 100%; height: 355px;
    background: linear-gradient(135deg, var(--pattern-shadow) 0%, var(--pattern-bronze) 50%, var(--pattern-shadow) 100%);
    opacity: .55;
  }
  .label-frame {
    position: absolute; left: 96px; top: 122px;
    width: 262px; height: 288px;
    background: var(--tin-black);
    border: 2px solid var(--frame-bronze);
  }
  .label-panel {
    position: absolute; left: 10px; top: 10px; right: 10px; bottom: 10px;
    background: var(--label-burgundy);
    border: 2px solid var(--frame-bronze);
    text-align: center;
  }
  .brand-name {
    position: absolute; left: 0; right: 0; top: 68px;
    font-family: "Montserrat", sans-serif; font-weight: 300;
    font-size: 44px; letter-spacing: 3px; line-height: 1;
    color: var(--brand-champagne);
  }
  .tea-variety {
    position: absolute; left: 0; right: 0; top: 125px;
    font-family: "Libre Baskerville", serif; font-weight: 700;
    font-size: 23px; letter-spacing: 1.5px; line-height: 1.2;
    color: var(--label-ivory);
  }
  .tea-tagline {
    position: absolute; left: 0; right: 0; top: 155px;
    font-family: "Libre Baskerville", serif; font-style: italic;
    font-size: 17px; letter-spacing: .5px; line-height: 1.2;
    color: var(--label-ivory);
  }
  .origin-line {
    position: absolute; left: 0; right: 0; top: 194px;
    font-family: "Montserrat", sans-serif; font-weight: 400;
    font-size: 10px; letter-spacing: 2.5px; line-height: 1;
    color: var(--brand-champagne);
  }
  .pack-size {
    position: absolute; left: 0; right: 0; top: 222px;
    font-family: "Oswald", sans-serif; font-weight: 400;
    font-size: 12.5px; letter-spacing: 1px; line-height: 1.2;
    color: var(--label-ivory);
  }
</style>
</head>
<body>
  <main class="canvas">
    <section class="tin-face">
      <div class="rim-line"></div>
      <div class="pattern-field" role="img" aria-label="Bronze geometric lattice pattern on black"></div>
      <div class="label-frame">
        <div class="label-panel">
          <p class="brand-name">VELAN</p>
          <h1 class="tea-variety">GREEN TEA</h1>
          <p class="tea-tagline">Bold &amp; Uplifting</p>
          <p class="origin-line">PREMIUM KENYAN TEA</p>
          <p class="pack-size">25 BAGS , 50g</p>
        </div>
      </div>
    </section>
  </main>
</body>
</html>
```